Logistics Website Design

See website https://tqfreightglobal.com for theme and color details. Need the site to be re-done and reflect some of the designs shown in this list here: https://pixelvane.com/tags/logistics-company-website

Target Market(s)

Logistics & Transportation

Industry/Entity Type

Logistics and Supply Chain

Coding

Number of Pages Required

5+ page

Requirements
Must have
• Colors must match theme of logo. Looking for a sleek, interactive design.

```html
<!DOCTYPE html>
<html lang="en">
<head>
<meta charset="UTF-8">
<title>TQ Freight Global — Delivering Strength in Every Mile</title>
<link rel="stylesheet" href="https://fonts.googleapis.com/css2?family=Lato:wght@400;700&family=Merriweather+Sans:wght@700;800&display=swap">
<style>
:root{
  --orange:#e8693f;
  --orange-soft:#f08a66;
  --brown:#3b1a10;
  --ink:#1c1c1c;
  --text:#4a4a4a;
  --muted:#6b6b6b;
  --footer:#1a0e0a;
  --white:#ffffff;
  --line:#e6e6e6;
}
*{box-sizing:border-box;margin:0;padding:0}
html,body{width:1200px;height:3549px;overflow:hidden;background:var(--white)}
body{position:relative;font-family:'Lato',sans-serif;color:var(--text)}
.abs{position:absolute}
.head-font{font-family:'Merriweather Sans',sans-serif}

/* Header */
.nav-link{position:absolute;top:48px;font-size:15px;color:#444;text-decoration:none}
.nav-link.active{color:var(--orange)}
.nav-link.active::after{content:"";position:absolute;left:0;right:0;bottom:-6px;height:2px;background:var(--orange)}
.btn{position:absolute;display:flex;align-items:center;justify-content:center;border-radius:30px;font-weight:700;color:var(--white);font-size:15px;text-decoration:none}
.btn-orange{background:var(--orange)}
.btn-brown{background:var(--brown)}
.brand-tab{position:absolute;left:486px;top:-14px;width:218px;height:210px;border-radius:50%;background:var(--white);z-index:3;display:flex;align-items:center;justify-content:center;gap:8px}
.brand-dot{width:22px;height:22px;border-radius:50%;background:var(--orange)}
.brand-name{font-weight:700;font-size:19px;color:var(--brown);line-height:1.15;text-align:left}

/* Hero */
.hero{left:50px;top:117px;width:1086px;height:594px;border-radius:27px;overflow:hidden;
  background:linear-gradient(100deg,#eef0f2 0%,#e4e7ea 42%,#cfd3d8 60%,#b9bfc6 78%,#8d8781 100%)}
.hero-road{position:absolute;left:0;right:0;bottom:0;height:150px;background:linear-gradient(175deg,#8e8073 0%,#6d5f54 60%,#4d4540 100%)}
.hero-truck{position:absolute;left:560px;top:40px;width:526px;height:540px;border-radius:40px 0 0 0;background:linear-gradient(160deg,#f7f8f9 0%,#dde1e5 55%,#a9aeb4 100%)}
.hero h1{position:absolute;left:60px;top:140px;font-size:45px;line-height:56px;font-weight:800;color:#111}
.hero h1 span{color:var(--orange);display:block}
.hero p{position:absolute;left:62px;top:267px;font-size:22px;line-height:32px;color:#333;width:520px}
.dots{position:absolute;display:flex;gap:8px}
.dots i{display:block;width:22px;height:5px;background:#fff;border-radius:2px}

/* Section titles */
.sec-title{position:absolute;left:0;width:1200px;text-align:center;font-weight:800;font-size:35px;color:var(--ink)}
.sec-rule{position:absolute;height:3px;width:98px;background:var(--orange)}
.sec-intro{position:absolute;left:0;width:1200px;text-align:center;font-size:18px;line-height:25px;color:#444}

/* Service cards */
.svc{position:absolute;background:var(--white);border-radius:14px;box-shadow:0 4px 18px rgba(0,0,0,.12);padding:18px}
.svc h3{font-size:20px;font-weight:800;color:var(--ink)}
.svc .arrow{position:absolute;top:16px;right:18px;width:28px;height:28px;border-radius:50%;background:var(--orange);display:flex;align-items:center;justify-content:center}
.svc .photo{position:absolute;left:10px;right:10px;bottom:12px;border-radius:10px}
.svc.featured h3{color:var(--orange);font-size:20px}
.svc.featured p{font-size:15px;line-height:23px;color:#444;margin-top:12px}
.svc.featured .arrow{background:#111}
.carousel-btn{position:absolute;width:26px;height:26px;border-radius:50%;display:flex;align-items:center;justify-content:center}

/* Band */
.band{left:40px;top:1434px;width:1104px;height:446px;border-radius:26px;background:linear-gradient(90deg,#e8693f 0%,#e96e47 55%,#dc6440 100%);overflow:hidden}
.band h2{position:absolute;top:94px;left:0;width:100%;text-align:center;color:#fff;font-size:36px;font-weight:800}
.band p{position:absolute;top:165px;left:150px;width:804px;text-align:center;color:#fff;font-size:18.5px;line-height:26.5px}

/* About */
.about-photo{left:110px;top:2004px;width:408px;height:417px;border-radius:24px;background:linear-gradient(180deg,#b9a389 0%,#d9a66b 40%,#3b3f74 62%,#1f1f26 100%)}
.about h2{position:absolute;left:607px;top:1998px;font-size:35px;font-weight:800;color:var(--ink)}
.about p{position:absolute;left:607px;width:470px;font-size:17px;line-height:28px;text-align:justify;color:#444}

/* Industries */
.ind{position:absolute;top:2702px;width:232px;height:240px;background:var(--white);border-radius:6px;box-shadow:0 3px 14px rgba(0,0,0,.1);text-align:center;padding-top:20px}
.ind svg{display:block;margin:0 auto}
.ind h3{font-family:'Merriweather Sans',sans-serif;font-size:19px;font-weight:800;color:var(--ink);margin-top:10px}
.ind p{font-size:14.5px;line-height:23px;color:#555;margin:10px 14px 0}
.ind.active{background:var(--orange)}
.ind.active h3,.ind.active p{color:#fff}

/* Footer */
.footer{left:41px;top:3098px;width:1106px;height:382px;border-radius:28px;background:var(--footer)}
.footer .brand{position:absolute;left:0;width:100%;top:100px;display:flex;justify-content:center;align-items:center;gap:10px}
.footer .brand .brand-name{color:#fff;font-size:22px}
.foot-link{position:absolute;top:217px;color:#fff;font-size:15px}
.foot-icon{position:absolute;top:272px;width:36px;height:36px;display:flex;align-items:center;justify-content:center;border-radius:8px}
.foot-rule{position:absolute;top:349px;height:1px;background:#5a4a44}
.copy{position:absolute;top:340px;left:0;width:100%;text-align:center;color:#fff;font-size:13px}
</style>
</head>
<body>

<!-- Header -->
<header>
  <a class="nav-link active" style="left:125px">Home</a>
  <a class="nav-link" style="left:198px">About Us</a>
  <a class="nav-link" style="left:290px">Services</a>
  <a class="nav-link" style="left:369px">Industries</a>
  <a class="nav-link" style="left:755px">Contact Us</a>
  <svg class="abs" style="left:862px;top:46px" width="24" height="24" viewBox="0 0 24 24" fill="none" stroke="#222" stroke-width="2"><circle cx="10" cy="10" r="7"/><path d="M15 15l6 6"/></svg>
  <a class="btn btn-orange" style="left:911px;top:38px;width:165px;height:42px">Request a Quote</a>
  <div class="brand-tab"><span class="brand-dot"></span><span class="brand-name">TQ Freight<br>Global</span></div>
</header>

<!-- Hero -->
<section class="abs hero">
  <div class="hero-road"></div>
  <div class="hero-truck" role="img" aria-label="White semi truck with trailer driving on a highway"></div>
  <h1 class="head-font"><span>DELIVERING STRENGTH</span>IN EVERY MILE</h1>
  <p>Fast, secure, and reliable freight solutions designed to move your business forward—mile after mile.</p>
  <a class="btn btn-orange" style="left:59px;top:364px;width:160px;height:41px">Request a Quote</a>
  <a class="btn btn-brown" style="left:228px;top:364px;width:144px;height:41px">View Services</a>
  <div class="dots" style="left:506px;top:521px"><i></i><i></i><i></i></div>
</section>

<!-- Services -->
<section>
  <h2 class="sec-title head-font" style="top:812px">OUR SERVICES</h2>
  <div class="sec-rule" style="left:546px;top:861px"></div>
  <p class="sec-intro" style="top:880px">Comprehensive logistics solutions tailored to deliver efficiency, reliability,<br>and performance at every stage.</p>

  <div class="carousel-btn" style="left:85px;top:1187px;background:#f6c7b6">
    <svg width="12" height="12" viewBox="0 0 12 12" fill="none" stroke="#fff" stroke-width="2"><path d="M8 2L4 6l4 4"/></svg></div>
  <div class="carousel-btn" style="left:1077px;top:1187px;background:var(--orange)">
    <svg width="12" height="12" viewBox="0 0 12 12" fill="none" stroke="#fff" stroke-width="2"><path d="M4 2l4 4-4 4"/></svg></div>

  <article class="svc" style="left:124px;top:1049px;width:261px;height:265px">
    <h3 class="head-font">Flatbed</h3>
    <span class="arrow"><svg width="12" height="12" viewBox="0 0 12 12" fill="none" stroke="#fff" stroke-width="2"><path d="M3 9l6-6M4 3h5v5"/></svg></span>
    <div class="photo" role="img" aria-label="White trucks on a highway" style="top:58px;background:linear-gradient(180deg,#c9d2d9 0%,#a8b0a0 45%,#5e6461 100%)"></div>
  </article>

  <article class="svc featured" style="left:417px;top:964px;width:351px;height:350px">
    <h3 class="head-font">Step Deck Transportation</h3>
    <span class="arrow"><svg width="12" height="12" viewBox="0 0 12 12" fill="none" stroke="#fff" stroke-width="2"><path d="M3 9l6-6M4 3h5v5"/></svg></span>
    <p>Step deck trucking services support tall, heavy, specialized freight requiring height clearance and flexible loading options.</p>
    <div class="photo" role="img" aria-label="Red step deck trailer parked at a warehouse" style="top:143px;background:linear-gradient(180deg,#b8c4d0 0%,#8a8f98 45%,#c8453c 70%,#d9d6d2 100%)"></div>
  </article>

  <article class="svc" style="left:802px;top:1049px;width:261px;height:265px">
    <h3 class="head-font">Dry Van</h3>
    <span class="arrow"><svg width="12" height="12" viewBox="0 0 12 12" fill="none" stroke="#fff" stroke-width="2"><path d="M3 9l6-6M4 3h5v5"/></svg></span>
    <div class="photo" role="img" aria-label="White dry van truck on a rural road" style="top:58px;background:linear-gradient(180deg,#dfd8d2 0%,#c2b8b0 50%,#6f6a66 100%)"></div>
  </article>
</section>

<!-- Supply chain band -->
<section class="abs band" role="img" aria-label="Orange tinted photo of trucks on the road">
  <h2 class="head-font">KEEPING YOUR SUPPLY CHAIN MOVING</h2>
  <p>We deliver a comprehensive range of open-deck and specialized transportation services—including flatbed, step deck, heavy haul, and over-dimensional freight solutions. Backed by years of experience, a trusted nationwide carrier network, and a strong safety-first culture, we provide reliable, adaptable logistics support built around the unique requirements of every load.</p>
  <a class="btn btn-brown" style="left:473px;top:302px;width:158px;height:41px">Request a Quote</a>
</section>

<!-- About -->
<section class="about">
  <div class="abs about-photo" role="img" aria-label="Blue semi truck driving on a highway at sunset"></div>
  <h2 class="head-font">ABOUT US</h2>
  <div class="sec-rule" style="left:607px;top:2048px"></div>
  <p style="top:2076px">TQ Freight Global™ was born out of real-world experience in the fitness equipment industry. What started as a company shipping strength equipment, cardio machines, and training gear to gyms, schools, and commercial facilities quickly evolved into something bigger.</p>
  <p style="top:2234px">As order volume grew and supply chains became more complex, the team developed deep expertise in coordinating freight, managing deliveries, and navigating the challenges of large-scale equipment transportation.</p>
  <a class="btn btn-orange" style="left:607px;top:2375px;width:134px;height:41px">Read More</a>
</section>

<!-- Industries -->
<section>
  <h2 class="sec-title head-font" style="top:2550px">OUR INDUSTRIES</h2>
  <div class="sec-rule" style="left:546px;top:2599px"></div>
  <p class="sec-intro" style="top:2618px">Comprehensive logistics solutions tailored to deliver efficiency, reliability,<br>and performance at every stage.</p>

  <article class="ind" style="left:110px">
    <svg width="60" height="58" viewBox="0 0 60 58" fill="none" stroke="#e8693f" stroke-width="2.5"><path d="M6 4v18c0 4 6 4 6 0V4M9 22v32M50 4v50M50 4c-6 4-6 18 0 22"/><circle cx="30" cy="30" r="13"/><circle cx="30" cy="30" r="7"/></svg>
    <h3>Food &amp; Beverage</h3>
    <p>TQ Freight provides reliable, compliant, and efficient trucking solutions for the food and beverage industry.</p>
  </article>
  <article class="ind active" style="left:356px">
    <svg width="60" height="58" viewBox="0 0 60 58" fill="none" stroke="#fff" stroke-width="2.5"><path d="M8 6h44l4 12H4zM4 18c0 6 10 6 10 0 0 6 10 6 10 0 0 6 12 6 12 0 0 6 10 6 10 0 0 6 10 6 10 0"/><path d="M8 26v28h44V26M14 32h14v14H14zM34 32h12v22"/></svg>
    <h3>E-commerce &amp; Retail</h3>
    <p>E-Commerce &amp; Retail Trucking Services support fast-paced logistics demands of retailers and brands.</p>
  </article>
  <article class="ind" style="left:600px">
    <svg width="60" height="58" viewBox="0 0 60 58" fill="none" stroke="#e8693f" stroke-width="2.5"><path d="M4 54h52M6 54V26l12 8v-8l12 8v-8l12 8V6h8v48"/><path d="M12 42h6M24 42h6M36 42h6M12 48h6M24 48h6M36 48h6"/></svg>
    <h3>Manufacturing</h3>
    <p>Industrial machinery and processing equipment often present unique challenges due to size, weight, and design.</p>
  </article>
  <article class="ind" style="left:846px">
    <svg width="60" height="58" viewBox="0 0 60 58" fill="none" stroke="#e8693f" stroke-width="2.5"><circle cx="32" cy="24" r="13"/><path d="M32 17v14M25 24h14M4 44l10-6h14l6 4H22M14 52l8-4h18l14-12"/></svg>
    <h3>Pharma &amp; Healthcare</h3>
    <p>TQ Freight provides reliable, compliant, and efficient trucking solutions for the food and beverage industry.</p>
  </article>
  <div class="dots" style="left:555px;top:2976px"><i style="background:var(--orange)"></i><i style="background:#999"></i><i style="background:#999"></i></div>
</section>

<!-- Footer -->
<footer class="abs footer">
  <div class="brand"><span class="brand-dot"></span><span class="brand-name">TQ Freight Global</span></div>
  <span class="foot-link" style="left:285px">Home</span>
  <span class="foot-link" style="left:384px">About Us</span>
  <span class="foot-link" style="left:509px">Services</span>
  <span class="foot-link" style="left:625px">Industries</span>
  <span class="foot-link" style="left:753px">Contact Us</span>
  <span class="foot-icon" style="left:459px;background:var(--orange)">
    <svg width="22" height="22" viewBox="0 0 24 24" fill="none" stroke="#fff" stroke-width="1.8"><circle cx="12" cy="12" r="9"/><path d="M3 12h18M12 3c3 3 3 15 0 18M12 3c-3 3-3 15 0 18"/></svg></span>
  <span class="foot-icon" style="left:538px">
    <svg width="22" height="18" viewBox="0 0 22 18"><rect x="1" y="2" width="20" height="14" rx="2" fill="#fff"/><path d="M2 3l9 7 9-7" fill="none" stroke="#1a0e0a" stroke-width="1.8"/></svg></span>
  <span class="foot-icon" style="left:619px">
    <svg width="20" height="20" viewBox="0 0 24 24"><path fill="#fff" d="M6.6 10.8a15 15 0 006.6 6.6l2.2-2.2c.3-.3.7-.4 1-.2 1.1.4 2.3.6 3.6.6.6 0 1 .4 1 1V20c0 .6-.4 1-1 1A17 17 0 013 4c0-.6.4-1 1-1h3.5c.6 0 1 .4 1 1 0 1.3.2 2.5.6 3.6.1.3 0 .7-.2 1z"/></svg></span>
  <div class="foot-rule" style="left:72px;width:263px"></div>
  <div class="foot-rule" style="left:775px;width:263px"></div>
  <p class="copy">Copyright © 2026 TQ Freight Global. All rights reserved.</p>
</footer>

</body>
</html>
```